Business Card Design Project

We are not a new company, but renamed to "Vantorin Kitchens" last year. We specialize in modern high-end cabinetry imports. We would like to communicate a sense of quality and cutting edge technology. Ideally the design would incorporate our logo colors, silver, red and preferably a black, matte background. Though we are open to suggestions.
Logo is attached.
Edit: I have attached rough drafts of the previous cards, this way you will have all necessary content that needs to go on the cards.
Updates
Project Deadline Extended
Reason: We have received a lot of great designs, but due to the sheer number we couldn't respond to all. We will extend the deadline for another 7 days to finalize and provide feedback to designers.
Thank you for your hard work!
Industry/Entity Type
Business
Look and feel
Each slider illustrates characteristics of the customer's brand and the style your logo design should communicate.

```html
<!DOCTYPE html>
<html lang="en">
<head>
<meta charset="utf-8">
<title>Vantorin Kitchens – Business Card</title>
<link rel="stylesheet" href="https://fonts.googleapis.com/css2?family=Ubuntu:wght@300;400;500;700&display=swap">
<style>
  :root {
    --card-bg-light: #2a2a2a;
    --card-bg-mid: #181818;
    --card-bg-dark: #0b0b0b;
    --frame: #8a8a8a;
    --silver: #c4c4c4;
    --silver-soft: #b2b2b2;
    --silver-block: #a3a3a3;
    --accent-red: #d8262c;
  }
  html, body {
    margin: 0;
    padding: 0;
    width: 1200px;
    height: 735px;
    overflow: hidden;
    background: #ffffff;
  }
  .card {
    position: relative;
    width: 1200px;
    height: 735px;
    box-sizing: border-box;
    border: 2px solid var(--frame);
    overflow: hidden;
    font-family: "Ubuntu", sans-serif;
  }
  .card-surface {
    position: absolute;
    inset: 0;
    background:
      radial-gradient(ellipse 70% 60% at 50% 45%, var(--card-bg-light) 0%, var(--card-bg-mid) 60%, var(--card-bg-dark) 100%);
  }
  .brand-block {
    position: absolute;
    left: 540px;
    top: 185px;
    width: 140px;
    height: 140px;
    background: var(--silver-block);
  }
  .brand-name {
    position: absolute;
    left: 0;
    right: 0;
    top: 360px;
    margin: 0;
    padding-left: 12px;
    text-align: center;
    font-size: 84px;
    font-weight: 400;
    font-variant: small-caps;
    letter-spacing: 12px;
    line-height: 1;
    white-space: nowrap;
    color: var(--silver);
  }
  .divider {
    position: absolute;
    left: 48px;
    top: 510px;
    width: 1097px;
    height: 3px;
  }
  .person {
    position: absolute;
    left: 0;
    right: 0;
    top: 562px;
    text-align: center;
  }
  .person-name {
    margin: 0;
    font-size: 48px;
    font-weight: 700;
    letter-spacing: 1px;
    line-height: 1.1;
    color: var(--silver);
  }
  .person-title {
    margin: 4px 0 0;
    font-size: 42px;
    font-weight: 400;
    line-height: 1.1;
    color: var(--silver-soft);
  }
</style>
</head>
<body>
  <main class="card">
    <div class="card-surface" role="img" aria-label="Dark brushed wood-grain texture background"></div>

    <div class="brand-block" aria-hidden="true"></div>
    <h1 class="brand-name">Vantorin Kitchens</h1>

    <svg class="divider" viewBox="0 0 1097 3" preserveAspectRatio="none" aria-hidden="true">
      <rect x="0" y="0" width="1097" height="3" fill="var(--accent-red)"/>
    </svg>

    <section class="person">
      <p class="person-name">MAREK DOVLIN</p>
      <p class="person-title">President</p>
    </section>
  </main>
</body>
</html>
```